Garlic Farm for Farm Sales/Restaurant sales

Need a professional, but appealing to agriculture world. We are selling 27 kinds of Organic Garlic from a farm in Simla,CO. I have uploaded logo and business information-we are going to need a template, because I will need to use it for four separate people.
-We are trying to appeal to Farm to table restaurants
-As well as growers/farmers

Target Market(s)

Agriculture Sales/Restaurants-Organic

Industry/Entity Type

Agriculture

Contact Information for Business Card

Want it to look more unique then your average kelto stock card- I want it to look amazing

Font styles to use
Sans Serif

Colors
0455a3
ec1f27
fbed22
ffffff

Requirements
Must have
• Just be creative
Nice to have
• Colorful
Should not have
• plain

```html
<!DOCTYPE html>
<html lang="en">
<head>
<meta charset="utf-8">
<title>Summit Ridge Garlic – Business Card</title>
<link rel="stylesheet" href="https://fonts.googleapis.com/css2?family=Questrial&family=Kalam:wght@400;700&display=swap">
<style>
  :root{
    --navy:#1c2f5e;
    --red:#c8102e;
    --yellow:#fbd400;
    --white:#ffffff;
    --stage:#e9e7e2;
    --shadow:rgba(20,25,40,.22);
  }
  *{margin:0;padding:0;box-sizing:border-box}
  html,body{width:1200px;height:950px;overflow:hidden}
  body{background:var(--stage);font-family:"Questrial",sans-serif;position:relative}

  .card{position:absolute;left:250px;width:700px;height:400px;border-radius:26px;overflow:hidden;box-shadow:0 14px 30px var(--shadow)}
  .card svg{position:absolute;inset:0;display:block}
  .card--front{top:50px;background:var(--white)}
  .card--back{top:500px;background:var(--navy)}

  /* front: brand block, kept clear of the wave */
  .brand{position:absolute;left:36px;top:150px;display:flex;align-items:center;gap:14px}
  .brand__dot{width:52px;height:52px;border-radius:50%;background:var(--red);flex:none}
  .brand__name{color:var(--navy);font-size:26px;line-height:1.1;letter-spacing:.5px}

  /* front: contact block */
  .contact{position:absolute;right:56px;top:56px;color:var(--white);font-size:18px;line-height:1.6;text-align:right}
  .contact__name{font-family:"Kalam",cursive;font-weight:700;color:var(--yellow);font-size:26px;line-height:1.2}
  .contact__role{margin-bottom:8px}
  .contact__row{display:flex;align-items:center;justify-content:flex-end;gap:10px}
  .contact__icon{width:16px;height:16px;flex:none}

  /* back */
  .back-brand{position:absolute;right:60px;bottom:100px;color:var(--white);font-size:44px;line-height:1}
  .social{position:absolute;right:60px;bottom:52px;display:flex;gap:10px}
  .social__dot{width:20px;height:20px;border-radius:50%;border:2px solid var(--white)}
</style>
</head>
<body>

<section class="card card--front" aria-label="Card front">
  <svg width="700" height="400" viewBox="0 0 700 400" aria-hidden="true">
    <path d="M338 0 C272 110 300 250 200 320 C140 362 70 382 0 388 L0 400 L700 400 L700 0 Z" fill="var(--red)"/>
    <path d="M364 0 C298 110 326 258 222 330 C160 372 80 392 0 398 L0 400 L700 400 L700 0 Z" fill="var(--white)"/>
    <path d="M372 0 C306 112 334 262 230 334 C168 376 86 396 0 402 L700 402 L700 0 Z" fill="var(--navy)"/>
  </svg>

  <div class="brand">
    <span class="brand__dot"></span>
    <p class="brand__name">Summit<br>Ridge<br>Garlic</p>
  </div>

  <div class="contact">
    <p class="contact__name">Daniel Reyes</p>
    <p class="contact__role">CEO/Founder</p>
    <p>P.O. Box 48</p>
    <p>Elbert, CO 80899</p>
    <p class="contact__row">719-555-0142
      <svg class="contact__icon" viewBox="0 0 16 16" aria-hidden="true"><path d="M4 1.5l2.2 3-1.4 1.6c.8 1.8 2.2 3.3 4 4.2l1.6-1.4 3 2.2-1.3 2.6C6.8 13.4 2.6 9.2 1.4 3z" fill="var(--yellow)"/></svg>
    </p>
    <p class="contact__row">hello@ridgegarlic.com
      <svg class="contact__icon" viewBox="0 0 16 16" aria-hidden="true"><rect x="1" y="3" width="14" height="10" rx="1.5" fill="var(--yellow)"/><path d="M1.5 4l6.5 5 6.5-5" fill="none" stroke="var(--navy)" stroke-width="1.4"/></svg>
    </p>
    <p class="contact__row">www.ridgegarlic.com
      <svg class="contact__icon" viewBox="0 0 16 16" aria-hidden="true"><circle cx="8" cy="8" r="7" fill="var(--yellow)"/><path d="M1 8h14M8 1c-3 3.5-3 10.5 0 14M8 1c3 3.5 3 10.5 0 14" fill="none" stroke="var(--navy)" stroke-width="1.1"/></svg>
    </p>
  </div>
</section>

<section class="card card--back" aria-label="Card back">
  <svg width="700" height="400" viewBox="0 0 700 400" aria-hidden="true">
    <path d="M380 0 L700 0 L700 150 C600 110 470 80 380 0 Z" fill="var(--red)"/>
    <circle cx="250" cy="40" r="150" fill="var(--yellow)"/>
  </svg>
  <p class="back-brand">Summit Ridge Garlic</p>
  <div class="social" aria-hidden="true">
    <span class="social__dot"></span><span class="social__dot"></span><span class="social__dot"></span><span class="social__dot"></span>
  </div>
</section>

</body>
</html>
```